Veldmark Supplies Business Card

Professional business card that stand out to our potential customers. Front and back with clean modern design

Industry/Entity Type

Oil and gas

Contact Information for Business Card

Name, address, website , office phone and cell number

Requirements
Must have
• Editable files for each employee

```html
<!DOCTYPE html>
<html lang="en">
<head>
<meta charset="utf-8">
<title>Veldmark Supplies Business Card</title>
<link rel="stylesheet" href="https://fonts.googleapis.com/css2?family=Montserrat:wght@400;500;800&display=swap">
<style>
  :root {
    --stage: #e7e5e2;
    --card: #2a2a2c;
    --card-back: #1c1c1e;
    --red: #ec1f27;
    --cyan: #12aed3;
    --ink: #ffffff;
    --ink-soft: #e6e6e6;
  }
  * { margin: 0; padding: 0; box-sizing: border-box; }
  html, body { width: 1200px; height: 900px; overflow: hidden; }
  body {
    background: var(--stage);
    font-family: "Montserrat", sans-serif;
    position: relative;
  }
  .card {
    position: absolute;
    width: 600px;
    height: 343px;
    border-radius: 22px;
    overflow: hidden;
    box-shadow: 0 14px 30px rgba(0,0,0,.28);
  }
  /* back side */
  .card-back {
    left: 110px;
    top: 80px;
    background: var(--card-back);
  }
  .back-pattern-area {
    position: absolute;
    inset: 0;
    background: linear-gradient(115deg, #9a9a9c 0%, #5e5e60 35%, #2c2c2e 65%, #121213 100%);
  }
  .back-brand {
    position: absolute;
    right: 150px;
    top: 150px;
    display: flex;
    align-items: center;
    gap: 8px;
    color: var(--red);
    font-weight: 800;
    font-size: 15px;
    letter-spacing: .5px;
    text-transform: uppercase;
  }
  .back-brand .mark-square { width: 12px; height: 12px; background: var(--cyan); }

  /* front side */
  .card-front {
    left: 490px;
    top: 470px;
    background: var(--card);
  }
  .front-brand {
    position: absolute;
    left: 40px;
    top: 150px;
    width: 190px;
    display: flex;
    align-items: center;
    gap: 10px;
    color: var(--ink);
    font-weight: 800;
    font-size: 21px;
    line-height: 1.15;
    text-transform: uppercase;
  }
  .front-brand .mark-square { flex: none; width: 22px; height: 22px; background: var(--red); }
  .divider {
    position: absolute;
    left: 258px;
    top: 58px;
    width: 2px;
    height: 240px;
    background: var(--red);
  }
  .details {
    position: absolute;
    left: 285px;
    top: 60px;
    color: var(--ink-soft);
  }
  .person-name {
    color: var(--red);
    font-weight: 800;
    font-size: 25px;
    letter-spacing: .5px;
    text-transform: uppercase;
    line-height: 1;
  }
  .person-role { font-size: 15px; margin-top: 6px; color: var(--ink); }
  .address { font-size: 14px; line-height: 1.35; margin-top: 16px; }
  .contact-list { list-style: none; margin-top: 14px; }
  .contact-list li {
    display: flex;
    align-items: center;
    gap: 10px;
    font-size: 14px;
    height: 23px;
  }
  .contact-icon {
    width: 18px; height: 16px;
    background: var(--red);
    display: flex; align-items: center; justify-content: center;
    flex: none;
  }
  .contact-icon svg { width: 12px; height: 12px; }
</style>
</head>
<body>

<section class="card card-back" aria-label="Card back">
  <div class="back-pattern-area" role="img" aria-label="Repeating brand-mark pattern fading from silver to black"></div>
  <div class="back-brand"><span class="mark-square"></span>Veldmark Supplies</div>
</section>

<section class="card card-front" aria-label="Card front">
  <div class="front-brand"><span class="mark-square"></span><span>Veldmark Supplies</span></div>
  <div class="divider"></div>
  <div class="details">
    <p class="person-name">Dorran Kessley</p>
    <p class="person-role">President</p>
    <p class="address">482 Hollister Ave, Ste<br>210, Odessa, TX 79761</p>
    <ul class="contact-list">
      <li><span class="contact-icon"><svg viewBox="0 0 12 12"><path d="M2 3c0-1 1-1.5 2-1.5l1 2-1 1c.5 1 1.5 2 2.5 2.5l1-1 2 1c0 1-.5 2-1.5 2C4.5 9 2 6.5 2 3z" fill="#fff"/></svg></span>432-555-0184</li>
      <li><span class="contact-icon"><svg viewBox="0 0 12 12"><rect x="3.5" y="1" width="5" height="10" rx="1" fill="none" stroke="#fff" stroke-width="1.2"/><circle cx="6" cy="9.3" r=".6" fill="#fff"/></svg></span>000-000-9999</li>
      <li><span class="contact-icon"><svg viewBox="0 0 12 12"><rect x="1" y="2.5" width="10" height="7" fill="none" stroke="#fff" stroke-width="1.1"/><path d="M1 2.5l5 4 5-4" fill="none" stroke="#fff" stroke-width="1.1"/></svg></span>info@example-youremail.com</li>
      <li><span class="contact-icon"><svg viewBox="0 0 12 12"><circle cx="6" cy="6" r="4.6" fill="none" stroke="#fff" stroke-width="1.1"/><ellipse cx="6" cy="6" rx="2" ry="4.6" fill="none" stroke="#fff" stroke-width="1"/><path d="M1.4 6h9.2" stroke="#fff" stroke-width="1"/></svg></span>www.example-yourwebsite.com</li>
    </ul>
  </div>
</section>

</body>
</html>
```